Hop Bright Meadow Business Website Branding

Looking for a wordpress template design with CSS and HTML encoding. Current website can be seen at hopbrightmeadow.example.

WE ARE CURRENTLY IN PROCESS GETTING A LOGO DESIGN... I HAVE INCLUDED THE TOP POTENTIAL DESIGNS FOR REFERENCE TO HELP UNDERSTAND WHAT STYLE WE ARE LOOKING FOR...
NOTE: THE “PEBBLE CREW” LOGO WAS A PREVIOUS COMPANY WE OWNED SO YOU CAN GE A FEEL FOR THE TYPE OF DESIGNS WE HAVE USED IN THE PAST.

My blog will focus on making a connection with wild Florida, it’s wildlife, plants and animals... with an eye toward Florida conservation, nature adventure trips, and education... Content, photos and other merchandise will also be offered for sale.
I’m looking for a site design that incorporates Florida nature and wildlife/plants, with a fun “Old Florida” retro-adventure feel.
When they see this site it should speak to the import of natural Florida and the critical nature of the ecosystem here... while being instantly recognizable and iconic... IE: when I think of florida I think of water, plants, warmth, sunsets etc...

https://join.chatroomhub.example/t/lumexstudio-kzt4821/shared_invite/zt-pqwrt83m-hRnLvXaKoPzsYcB1Uq7JdM

Target Market(s)

Nature, Education, Conservation, Photography

Industry/Entity Type

Photographer

Coding

Coded - Design and coding required

Requirements
Must have
• Need to have site wide template design which generally includes a landing page and a general page template for other pages... Must include html and css encoding...
Should not have
• Any animals included in the site should be Florida native... IE: no African animals etc... This will require some research to ensure that if animals are included that they are part of the Florida ecosystem.

```html
<!DOCTYPE html>
<html lang="en">
<head>
<meta charset="utf-8">
<title>Hop Bright Meadow</title>
<link href="https://fonts.googleapis.com/css2?family=Khand:wght@500;600;700&family=Roboto+Slab:wght@400;500;600&display=swap" rel="stylesheet">
<style>
:root{
  --cream:#ede6d2;
  --paper:#e6e3dc;
  --ink:#1a1410;
  --orange:#e8891a;
  --rule:#9c9a8c;
  --footer:#d6c6a8;
  --brown:#5a3a1a;
}
*{margin:0;padding:0;box-sizing:border-box}
html,body{width:1200px;height:4034px;overflow:hidden}
body{background:var(--cream);color:var(--ink);font-family:"Roboto Slab",serif;position:relative}
.abs{position:absolute}
.display{font-family:"Khand",sans-serif;font-weight:700;color:var(--ink);text-shadow:2px 2px 0 var(--orange);text-transform:uppercase;white-space:nowrap}
.label{font-family:"Khand",sans-serif;font-weight:700;text-transform:uppercase;color:var(--ink);text-shadow:1px 1px 0 var(--orange);letter-spacing:.5px;white-space:nowrap}

.rule-line{height:2px;background:var(--ink)}
.rule-line.soft{height:1.5px;background:var(--rule)}

/* navigation */
.nav-link{font-size:20px;line-height:24px;top:38px}
.nav-star{color:var(--orange);font-size:18px;line-height:22px;top:39px}
.brand{left:525px;top:18px;width:150px;text-align:center}
.brand-dot{width:18px;height:18px;border-radius:50%;background:var(--orange);margin:0 auto 4px}
.brand-name{font-family:"Khand",sans-serif;font-weight:700;font-size:20px;line-height:20px;color:var(--ink);text-transform:uppercase}

.photo{border-radius:2px}
.hero-photo{left:111px;top:123px;width:978px;height:430px;background:linear-gradient(180deg,#3f6a2a 0%,#2f3a32 40%,#4a4438 60%,#3d5a2c 100%);clip-path:polygon(0 0,100% 0,100% 98%,97% 100%,94% 98%,91% 100%,88% 98%,85% 100%,82% 98%,79% 100%,76% 98%,73% 100%,70% 98%,67% 100%,64% 98%,61% 100%,58% 98%,55% 100%,52% 98%,49% 100%,46% 98%,43% 100%,40% 98%,37% 100%,34% 98%,31% 100%,28% 98%,25% 100%,22% 98%,19% 100%,16% 98%,13% 100%,10% 98%,7% 100%,4% 98%,1% 100%,0 98%)}

.site-title{left:0;width:1200px;top:598px;text-align:center;font-size:60px;line-height:64px;letter-spacing:2px}
.site-tagline{left:0;width:1200px;top:698px;text-align:center;font-family:"Roboto Slab",serif;font-weight:600;font-size:19px;line-height:24px;text-transform:uppercase;text-shadow:1px 1px 0 var(--orange);letter-spacing:.5px}

.scroll-btn{left:571px;top:783px;width:58px;height:58px;border-radius:50%;background:var(--ink)}

.section-title{font-size:60px;line-height:64px}
.body-text{font-size:15.5px;line-height:28.5px;letter-spacing:.2px}

.btn{display:flex;align-items:center;justify-content:center;font-family:"Roboto Slab",serif;font-weight:600;font-size:15px;text-decoration:underline;color:var(--ink);text-shadow:1px 1px 0 var(--orange)}
.btn svg{position:absolute;left:0;top:0}

.paper{background:var(--paper)}
.torn{clip-path:polygon(1% 2%,6% 0,11% 2%,17% 0.5%,24% 1.5%,30% 0,37% 2%,44% 0.5%,51% 1.8%,58% 0,65% 1.5%,72% 0.3%,79% 2%,86% 0.5%,93% 1.8%,99% 0.3%,100% 8%,98.8% 18%,100% 30%,99% 42%,100% 55%,98.7% 68%,100% 80%,99% 92%,99.5% 99%,93% 98%,86% 100%,79% 98.5%,72% 99.8%,65% 98%,58% 99.7%,51% 98.2%,44% 100%,37% 98.5%,30% 99.8%,23% 98%,16% 99.8%,9% 98.3%,2% 99.5%,0.5% 92%,1.5% 80%,0 67%,1.3% 54%,0 41%,1.5% 28%,0.2% 15%)}

.card{background:rgba(237,230,210,.55)}
.card-title{font-family:"Roboto Slab",serif;font-weight:600;font-size:19px;line-height:24px;text-transform:uppercase;text-align:center;text-shadow:1px 1px 0 var(--orange);letter-spacing:.5px;white-space:nowrap}
.card-text{font-size:13.5px;line-height:23px;text-align:center}
.card-link{font-family:"Roboto Slab",serif;font-weight:600;font-size:14px;text-decoration:underline;text-align:center;text-shadow:1px 1px 0 var(--orange)}

.dots{display:flex;gap:6px}
.dot{width:13px;height:13px;border-radius:50%;border:1.5px dotted var(--ink)}
.dot.active{background:var(--orange);border:none}

.quote-mark{font-family:"Khand",sans-serif;font-weight:700;font-size:90px;line-height:60px;text-align:center;color:var(--ink);text-shadow:2px 2px 0 var(--orange)}
.quote-text{font-family:"Roboto Slab",serif;font-size:15.5px;line-height:27.5px;text-align:center}
.quote-name{font-family:"Roboto Slab",serif;font-weight:600;font-size:19px;line-height:24px;text-transform:uppercase;text-align:center;text-shadow:1px 1px 0 var(--orange);white-space:nowrap}

.footer{left:0;top:3862px;width:1200px;height:172px;background:var(--footer)}
.footer-link{font-size:21px;line-height:26px;top:46px}
.copyright{left:0;width:1200px;top:134px;text-align:center;font-size:15px;color:var(--brown)}
</style>
</head>
<body>

<header>
  <div class="abs rule-line" style="left:76px;top:26px;width:428px"></div>
  <div class="abs rule-line" style="left:76px;top:74px;width:428px"></div>
  <div class="abs rule-line" style="left:708px;top:26px;width:428px"></div>
  <div class="abs rule-line" style="left:708px;top:74px;width:428px"></div>
  <nav>
    <span class="abs label nav-link" style="left:110px">Home</span>
    <span class="abs nav-star" style="left:193px">★</span>
    <span class="abs label nav-link" style="left:238px">About Us</span>
    <span class="abs nav-star" style="left:356px">★</span>
    <span class="abs label nav-link" style="left:398px">My Blog</span>
    <span class="abs label nav-link" style="left:762px">Testimonials</span>
    <span class="abs nav-star" style="left:944px">★</span>
    <span class="abs label nav-link" style="left:1010px">Contact</span>
  </nav>
  <div class="abs brand">
    <div class="brand-dot"></div>
    <div class="brand-name">Hop Bright Meadow</div>
  </div>
</header>

<section class="hero">
  <div class="abs photo hero-photo" role="img" aria-label="Alligator resting on a log above still water with green foliage behind"></div>
  <h1 class="abs display site-title">Hop Bright Meadow</h1>
  <div class="abs rule-line" style="left:376px;top:677px;width:448px"></div>
  <p class="abs site-tagline">Exploring Florida's Natural Wonders</p>

  <div class="abs rule-line soft" style="left:110px;top:811px;width:448px"></div>
  <div class="abs rule-line soft" style="left:642px;top:811px;width:448px"></div>
  <div class="abs scroll-btn"></div>
  <svg class="abs" style="left:589px;top:804px" width="22" height="16" aria-hidden="true">
    <path d="M3 4 l8 8 l8 -8" fill="none" stroke="var(--orange)" stroke-width="3.5" stroke-linecap="round" stroke-linejoin="round"/>
  </svg>
</section>

<section class="about">
  <h2 class="abs display section-title" style="left:111px;top:922px">About Us</h2>
  <p class="abs body-text" style="left:111px;top:997px;width:470px">Come explore wild places and stunning scenery with me as I discover new and exciting eco-adventures and learn about the rare and unique wildlife and environments that make Florida so precious and extraordinary. I hope you can vicariously enjoy the wild and untamed beauty of Florida through my eyes, and learn some amazing things about nature on our explorations.</p>
  <div class="abs btn" style="left:112px;top:1223px;width:200px;height:46px">
    <svg width="200" height="46" aria-hidden="true"><path d="M8 2 H192 V14 l6 9 l-6 9 V44 H8 V32 l-6 -9 l6 -9 Z" fill="none" stroke="var(--ink)" stroke-width="1.5"/></svg>
    <span style="position:relative">READ MORE</span>
  </div>
  <svg class="abs" style="left:636px;top:904px" width="454" height="356" aria-hidden="true">
    <path d="M10 1 H444 l9 9 V346 l-9 9 H10 l-9 -9 V10 Z" fill="none" stroke="var(--ink)" stroke-width="2"/>
    <rect x="7" y="7" width="440" height="342" fill="none" stroke="var(--ink)" stroke-width="1.5"/>
  </svg>
  <div class="abs photo" style="left:648px;top:916px;width:430px;height:332px;background:linear-gradient(160deg,#7a6548 0%,#5c4a36 45%,#4d6a32 100%)" role="img" aria-label="Marsh rabbit sitting among leaf litter and green plants"></div>
</section>

<section class="blog">
  <div class="abs paper torn" style="left:95px;top:1355px;width:1020px;height:840px"></div>
  <h2 class="abs display section-title" style="left:0;width:1200px;text-align:center;top:1436px">Latest Blog</h2>
  <div class="abs rule-line" style="left:376px;top:1520px;width:448px"></div>

  <article class="abs card" style="left:128px;top:1575px;width:277px;height:460px">
    <svg class="abs" style="left:0;top:0" width="277" height="460" aria-hidden="true"><path d="M1 12 Q1 2 11 2 H266 Q276 2 276 12 M1 448 Q1 458 11 458 H266 Q276 458 276 448" fill="none" stroke="var(--ink)" stroke-width="2"/></svg>
    <div class="abs photo" style="left:2px;top:5px;width:273px;height:205px;background:linear-gradient(160deg,#6e7a68 0%,#e8603a 50%,#6b7260 100%);border-radius:6px" role="img" aria-label="Pink flamingo preening in shallow water"></div>
    <h3 class="abs card-title" style="left:0;width:277px;top:238px">Consequuntur Magni</h3>
    <p class="abs card-text" style="left:12px;width:253px;top:276px">Error sit voluptatem accusantium doloremque laudantium, totam rem aperiam, eaque ipsa quae ab illo inventore veritatis et quasi architecto beatae.</p>
    <p class="abs card-link" style="left:0;width:277px;top:408px">READ MORE</p>
  </article>

  <article class="abs card" style="left:458px;top:1575px;width:277px;height:460px">
    <svg class="abs" style="left:0;top:0" width="277" height="460" aria-hidden="true"><path d="M1 12 Q1 2 11 2 H266 Q276 2 276 12 M1 448 Q1 458 11 458 H266 Q276 458 276 448" fill="none" stroke="var(--ink)" stroke-width="2"/></svg>
    <div class="abs photo" style="left:2px;top:5px;width:273px;height:205px;background:linear-gradient(160deg,#4a5a3a 0%,#7a6a58 50%,#5a4a3a 100%);border-radius:6px" role="img" aria-label="Florida panther walking through a pine forest"></div>
    <h3 class="abs card-title" style="left:0;width:277px;top:238px">Ratione Voluptatem</h3>
    <p class="abs card-text" style="left:12px;width:253px;top:276px">Error sit voluptatem accusantium doloremque laudantium, totam rem aperiam, eaque ipsa quae ab illo inventore beatae.</p>
    <p class="abs card-link" style="left:0;width:277px;top:408px">READ MORE</p>
  </article>

  <article class="abs card" style="left:788px;top:1575px;width:277px;height:460px">
    <svg class="abs" style="left:0;top:0" width="277" height="460" aria-hidden="true"><path d="M1 12 Q1 2 11 2 H266 Q276 2 276 12 M1 448 Q1 458 11 458 H266 Q276 458 276 448" fill="none" stroke="var(--ink)" stroke-width="2"/></svg>
    <div class="abs photo" style="left:2px;top:5px;width:273px;height:205px;background:linear-gradient(180deg,#b8c4c8 0%,#8a9a5a 45%,#6a5238 70%,#8aa040 100%);border-radius:6px" role="img" aria-label="Wild turkey displaying its fanned tail in a grassy field"></div>
    <h3 class="abs card-title" style="left:0;width:277px;top:238px">Sequi Nesciunt</h3>
    <p class="abs card-text" style="left:12px;width:253px;top:276px">Error sit voluptatem accusantium doloremque laudantium, totam rem aperiam, eaque ipsa quae ab veritatis et quasi architecto beatae.</p>
    <p class="abs card-link" style="left:0;width:277px;top:408px">READ MORE</p>
  </article>

  <div class="abs dots" style="left:564px;top:2071px"><span class="dot"></span><span class="dot"></span><span class="dot active"></span><span class="dot"></span></div>
</section>

<section class="author">
  <svg class="abs" style="left:486px;top:2288px" width="260" height="342" aria-hidden="true">
    <rect x="1" y="1" width="257" height="339" fill="none" stroke="var(--ink)" stroke-width="2"/>
  </svg>
  <div class="abs photo" style="left:472px;top:2275px;width:258px;height:342px;background:linear-gradient(180deg,#8ea4b8 0%,#d89a6a 35%,#6a4a3a 55%,#2a9ab0 100%)" role="img" aria-label="Portrait of the blog author at the beach at sunset"></div>
  <p class="abs body-text" style="left:118px;top:2652px;width:964px;text-align:center">Hello nature lovers! I'm Marisol Pennick, a wildlife educator, Florida Master Naturalist, nature writer and photographer, busy mama of three kiddos, a playful Havanese puppy, two very chubby guinea pigs, and a giant tree frog. I have a passion for all things nature and I adore living in Southwest Florida. I will always be a California girl, but from the moment I set foot in Florida, its wild beauty stole my heart. For the past 23 years, I have been fortunate to have some very unique and special experiences caring for many different species of animals and educating the public about wildlife and the environment. My hope is that those I endeavor to educate will better understand their connection with the natural world and our shared responsibility to protect Florida's wild and priceless beauty.</p>
  <div class="abs btn" style="left:501px;top:2894px;width:200px;height:46px">
    <svg width="200" height="46" aria-hidden="true"><path d="M8 2 H192 V14 l6 9 l-6 9 V44 H8 V32 l-6 -9 l6 -9 Z" fill="none" stroke="var(--ink)" stroke-width="1.5"/></svg>
    <span style="position:relative">READ MORE</span>
  </div>
</section>

<section class="testimonials">
  <div class="abs paper torn" style="left:95px;top:3008px;width:1020px;height:805px"></div>
  <h2 class="abs display section-title" style="left:0;width:1200px;text-align:center;top:3096px">Testimonials</h2>
  <div class="abs rule-line" style="left:376px;top:3179px;width:448px"></div>

  <figure class="abs" style="left:108px;top:3262px;width:279px;height:350px">
    <svg class="abs" style="left:0;top:0" width="279" height="350" aria-hidden="true"><path d="M1 12 Q1 2 11 2 H268 Q278 2 278 12 M1 338 Q1 348 11 348 H268 Q278 348 278 338" fill="none" stroke="var(--ink)" stroke-width="2"/></svg>
    <div class="abs quote-mark" style="left:0;width:279px;top:50px">“</div>
    <blockquote class="abs quote-text" style="left:14px;width:251px;top:122px">“Nature has been for me, as long as I remember, a source of solace, inspiration, adventure, and delight; a home, a teacher, a companion.”</blockquote>
    <figcaption class="abs quote-name" style="left:0;width:279px;top:290px">Ellery Haddon</figcaption>
  </figure>

  <figure class="abs" style="left:458px;top:3262px;width:279px;height:350px">
    <svg class="abs" style="left:0;top:0" width="279" height="350" aria-hidden="true"><path d="M1 12 Q1 2 11 2 H268 Q278 2 278 12 M1 338 Q1 348 11 348 H268 Q278 348 278 338" fill="none" stroke="var(--ink)" stroke-width="2"/></svg>
    <div class="abs quote-mark" style="left:0;width:279px;top:50px">“</div>
    <blockquote class="abs quote-text" style="left:14px;width:251px;top:122px">“Nature has been for me, as long as I remember, a source of solace, inspiration, adventure, and delight; a home, a teacher, a companion.”</blockquote>
    <figcaption class="abs quote-name" style="left:0;width:279px;top:290px">Tobin Ashgrove</figcaption>
  </figure>

  <figure class="abs" style="left:808px;top:3262px;width:279px;height:350px">
    <svg class="abs" style="left:0;top:0" width="279" height="350" aria-hidden="true"><path d="M1 12 Q1 2 11 2 H268 Q278 2 278 12 M1 338 Q1 348 11 348 H268 Q278 348 278 338" fill="none" stroke="var(--ink)" stroke-width="2"/></svg>
    <div class="abs quote-mark" style="left:0;width:279px;top:50px">“</div>
    <blockquote class="abs quote-text" style="left:14px;width:251px;top:122px">“Nature has been for me, as long as I remember, a source of solace, inspiration, adventure, and delight; a home, a teacher, a companion.”</blockquote>
    <figcaption class="abs quote-name" style="left:0;width:279px;top:290px">Caspar Lindqvist</figcaption>
  </figure>

  <div class="abs dots" style="left:564px;top:3662px"><span class="dot"></span><span class="dot"></span><span class="dot active"></span><span class="dot"></span></div>
</section>

<footer class="abs footer">
  <span class="abs label footer-link" style="left:210px">Home</span>
  <span class="abs label footer-link" style="left:349px">About Us</span>
  <span class="abs label footer-link" style="left:523px">My Blog</span>
  <span class="abs label footer-link" style="left:686px">Testimonials</span>
  <span class="abs label footer-link" style="left:903px">Contact</span>
  <div class="abs" style="left:111px;top:102px;width:978px;height:1px;background:var(--rule)"></div>
  <p class="abs copyright">Copyrights © 2020 All Rights Reserved</p>
</footer>

</body>
</html>
```